Security company needs HTML and CSS files and templates made & Blogs

need HTML files and template pages created for about us, staff, MMJ transport, vehicles, alarm systems, video systems, gaurd services, private investigations, surveillance audit request form, and compliance investigation request form, blog setup for video systems, alarm systems, and video monitoring. Needs to be Adobe Dreamweaver CS6 Format. Website needs to be based off the original PSD file. All images must be original or royalty free for use.

Target Market(s)

Customers

Industry/Entity Type

Security

Coding

Coded - Design and coding required

Number of Pages Required

5+ page

Requirements
Must have
• template pages created for about us, staff, MMJ transport, vehicles, alarm systems, video systems, gaurd services, private investigations, surveillance audit request form, and compliance investigation request form, blog setup for video systems, alarm systems, and video monitoring. Needs to be Adobe Dreamweaver CS6 Format Website needs to be based off the original PSD file
Nice to have
• Scheduling calendar built in that interfaces with Brivolta Mailhub, Blogs

```html
<!DOCTYPE html>
<html lang="en">
<head>
<meta charset="utf-8">
<title>Vantor Guard – Contact Us</title>
<link href="https://fonts.googleapis.com/css2?family=Exo+2:ital,wght@1,800&family=Open+Sans:wght@400;600&family=Roboto:wght@400;500&display=swap" rel="stylesheet">
<style>
:root{
  --blue:#2ba3dd;
  --blue-dark:#0d77a6;
  --nav-top:#3bb3ea;
  --nav-bot:#1a8fcf;
  --lime:#8dc21f;
  --lime-dark:#6f9c12;
  --page:#efefef;
  --text:#333;
  --muted:#555;
  --navy:#0e2c54;
  --white:#fff;
}
*{box-sizing:border-box;margin:0;padding:0}
html,body{width:1128px;height:1200px;overflow:hidden}
body{position:relative;background:#fff;font-family:"Open Sans",sans-serif;color:var(--text)}
.abs{position:absolute}
.topline{left:0;top:0;width:1128px;height:4px;background:var(--blue)}
.contact-tab{left:668px;top:0;width:460px;height:36px;background:var(--blue);border-bottom-left-radius:18px;color:var(--white);font:500 15px "Roboto",sans-serif;display:flex;align-items:center;gap:32px;padding-left:26px}
.contact-tab span{display:flex;align-items:center;gap:10px}
.brand{left:93px;top:40px;display:flex;align-items:center;gap:10px;font:600 22px "Open Sans",sans-serif;color:#c8202a}
.brand i{width:26px;height:26px;border-radius:50%;background:#c8202a;display:block}
.top-nav{right:94px;top:84px;display:flex;gap:33px;font:400 16px "Roboto",sans-serif;color:#333}
.main-nav{left:0;top:143px;width:1128px;height:57px;background:linear-gradient(var(--nav-top),var(--nav-bot));border-bottom:3px solid var(--lime)}
.main-nav ul{list-style:none;display:flex;position:absolute;left:93px;top:0;height:54px;font:400 16px "Roboto",sans-serif;color:var(--white)}
.main-nav li{padding:0 18px 0 28px;display:flex;align-items:center}
.main-nav li+li{padding-left:18px}
.main-nav li.active{background:linear-gradient(#9ccc24,#6f9c12);padding:0 22px 0 28px}
.hero{left:0;top:200px;width:1128px;height:208px;background:radial-gradient(ellipse at 25% 20%,#1f4f86,var(--navy) 70%)}
.hero-cam{right:0;top:0;width:380px;height:208px;background:linear-gradient(135deg,transparent 30%,#6b7f95 60%,#1c2e45 90%);opacity:.6}
.hero-title{left:93px;top:276px;font:800 italic 41px/1 "Exo 2",sans-serif;color:var(--white);text-shadow:0 2px 4px rgba(0,0,0,.35)}
.content{left:0;top:408px;width:1128px;height:440px;background:var(--page)}
.field{background:#ececec;border:1px solid #bbb;font-size:12px;color:#444;padding:10px 14px}
.btn{background:linear-gradient(#93c41e,#6f9c12);color:var(--white);font:400 16px "Roboto",sans-serif;display:flex;align-items:center;justify-content:center;border-radius:3px}
.map{left:620px;top:460px;width:417px;height:178px;border:2px solid #ccc;background:linear-gradient(160deg,#f2ecd9,#e4e9d4 60%,#cde0ef)}
.addr h2{font:400 20px "Roboto",sans-serif;color:#333}
.addr-rule{left:628px;top:682px;width:294px;height:1px;background:#d9d9d9}
.addr p{font-size:12.5px;line-height:23px;color:var(--muted);letter-spacing:.3px}
.footer{left:0;top:848px;width:1128px;height:287px;background:var(--blue-dark);color:var(--white)}
.badge{left:99px;top:893px;width:128px;height:128px;border-radius:50%;background:#c9a02c;border:6px solid #1b2a4a}
.social{top:1047px;width:31px;height:31px;border:2px solid var(--white);border-radius:50%}
.f-head{top:900px;font:400 19px "Roboto",sans-serif;color:var(--white)}
.links{left:328px;top:944px;list-style:none;font:400 12px "Open Sans",sans-serif;line-height:24px;color:var(--white)}
.links li::before{content:">";margin-right:7px}
.fc{font-size:12px;line-height:19px;color:var(--white)}
.ffield{border:1px solid var(--white);border-radius:3px;font-size:11px;padding:10px 12px;color:var(--white)}
.bottom{left:0;top:1135px;width:1128px;height:65px;background:linear-gradient(#9ccc1a,#6f9c12);color:var(--white);font-size:14px;padding:30px 0 0 93px}
</style>
</head>
<body>
<div class="abs topline"></div>
<div class="abs contact-tab">
  <span><svg width="14" height="11" viewBox="0 0 14 11"><rect x="0.75" y="0.75" width="12.5" height="9.5" fill="none" stroke="#fff" stroke-width="1.5"/><path d="M1 1l6 5 6-5" fill="none" stroke="#fff" stroke-width="1.5"/></svg>info@vantorguard.example</span>
  <span><svg width="13" height="13" viewBox="0 0 24 24"><path fill="#fff" d="M6.6 10.8a15 15 0 006.6 6.6l2.2-2.2c.3-.3.7-.4 1-.2 1.1.4 2.3.6 3.6.6.6 0 1 .4 1 1V20c0 .6-.4 1-1 1A17 17 0 013 4c0-.6.4-1 1-1h3.5c.6 0 1 .4 1 1 0 1.3.2 2.5.6 3.6.1.3 0 .7-.2 1z"/></svg>+1 800 555 0142</span>
</div>
<div class="abs brand"><i></i>Vantor Guard</div>
<nav class="abs top-nav"><span>Private Investigations</span><span>Surveillance Audit</span><span>Compliance Investigations</span><span>Contact Us</span></nav>
<nav class="abs main-nav"><ul>
  <li class="active">Home</li><li>About Us</li><li>Our Staff</li><li>MMJ Trasnport &amp; Courier Services</li><li>Our Vehicles</li><li>Alarm Systems</li><li>Video Systems</li>
</ul></nav>
<div class="abs hero" role="img" aria-label="Night sky with a security camera mounted on the right"><div class="abs hero-cam"></div></div>
<h1 class="abs hero-title">Contact Us</h1>

<section class="abs content"></section>
<div class="abs field" style="left:93px;top:467px;width:237px;height:34px">Name</div>
<div class="abs field" style="left:352px;top:467px;width:237px;height:34px">Phone No</div>
<div class="abs field" style="left:93px;top:515px;width:237px;height:34px">Mail</div>
<div class="abs field" style="left:352px;top:515px;width:237px;height:34px">Subjects</div>
<div class="abs field" style="left:93px;top:563px;width:497px;height:160px">Message</div>
<div class="abs btn" style="left:92px;top:748px;width:142px;height:39px">SEND NOW</div>

<div class="abs map" role="img" aria-label="Street map of the office location"></div>
<div class="abs addr" style="left:628px;top:652px"><h2>ADDRESS</h2></div>
<div class="abs addr-rule"></div>
<div class="abs addr" style="left:630px;top:694px;width:300px"><p>Vantor Guard; 3rd Floor, 41 Harlow Lane, Eastmere.</p></div>
<div class="abs addr" style="left:630px;top:749px">
  <p><svg width="18" height="14" viewBox="0 0 24 24" style="vertical-align:-2px;margin-right:12px"><path fill="none" stroke="#999" stroke-width="1.4" d="M6.6 10.8a15 15 0 006.6 6.6l2.2-2.2c.3-.3.7-.4 1-.2 1.1.4 2.3.6 3.6.6.6 0 1 .4 1 1V20c0 .6-.4 1-1 1A17 17 0 013 4c0-.6.4-1 1-1h3.5c.6 0 1 .4 1 1 0 1.3.2 2.5.6 3.6.1.3 0 .7-.2 1z"/></svg>Phone: +1 800 555 0142</p>
  <p style="margin-top:3px"><svg width="18" height="13" viewBox="0 0 18 13" style="vertical-align:-2px;margin-right:12px"><rect x="0.7" y="0.7" width="16.6" height="11.6" fill="none" stroke="#999" stroke-width="1.2"/><path d="M1 1l8 6 8-6M1 12l6-5M17 12l-6-5" fill="none" stroke="#999" stroke-width="1.2"/></svg>Email: info@vantorguard.example</p>
</div>

<footer class="abs footer"></footer>
<div class="abs badge" role="img" aria-label="Partner badge"></div>
<div class="abs social" style="left:94px"></div>
<div class="abs social" style="left:131px"></div>
<div class="abs social" style="left:167px"></div>
<div class="abs social" style="left:204px"></div>
<h3 class="abs f-head" style="left:328px">QUICK LINK</h3>
<ul class="abs links"><li>Home</li><li>About Us</li><li>Services</li><li>Blog</li><li>News</li><li>Contact Us</li></ul>
<h3 class="abs f-head" style="left:511px">CONTACT US</h3>
<div class="abs fc" style="left:513px;top:942px">
  <svg width="12" height="16" viewBox="0 0 12 16" style="position:absolute;left:0;top:2px"><path fill="#8dc21f" d="M6 0a6 6 0 016 6c0 4-6 10-6 10S0 10 0 6a6 6 0 016-6z"/><circle cx="6" cy="6" r="2.3" fill="#0d77a6"/></svg>
  <div style="margin-left:24px"><span style="font-size:14px">Vantor Guard,</span><br>3rd Floor, 41 Harlow Lane,<br>Eastmere,</div>
  <div style="margin-top:14px;font-size:14px"><svg width="13" height="13" viewBox="0 0 24 24" style="vertical-align:-1px;margin-right:8px"><path fill="#8dc21f" d="M6.6 10.8a15 15 0 006.6 6.6l2.2-2.2c.3-.3.7-.4 1-.2 1.1.4 2.3.6 3.6.6.6 0 1 .4 1 1V20c0 .6-.4 1-1 1A17 17 0 013 4c0-.6.4-1 1-1h3.5c.6 0 1 .4 1 1 0 1.3.2 2.5.6 3.6.1.3 0 .7-.2 1z"/></svg>Help:&nbsp;&nbsp; +1 800 555 0142</div>
  <div style="margin-top:16px;font-size:14px"><svg width="13" height="10" viewBox="0 0 13 10" style="margin-right:10px"><rect width="13" height="10" fill="#8dc21f"/><path d="M0 0l6.5 5L13 0" fill="none" stroke="#0d77a6"/></svg>Mail:&nbsp;&nbsp; info@vantorguard.example</div>
</div>
<h3 class="abs f-head" style="left:782px">CONTACT FORM</h3>
<div class="abs ffield" style="left:783px;top:943px;width:123px;height:34px">Name</div>
<div class="abs ffield" style="left:912px;top:943px;width:123px;height:34px">Phone</div>
<div class="abs ffield" style="left:783px;top:983px;width:252px;height:62px">Message</div>
<div class="abs btn" style="left:783px;top:1059px;width:112px;height:36px;font-size:12px;background:var(--lime);border-radius:2px">SEND MESSAGE</div>
<div class="abs bottom">© 2016 Vantor Guard.All Rights Reserved.</div>
</body>
</html>
```